Telecommunications/Power civil contractor needs business card design

Were a new telecommunications/power underground civil contractor that is looking for a new business card design. Our company colours are silver or grey and orange. Feel free to use the white background logo or the black background logo.

Target Market(s)

Local contractors, utility companies, private sector mining/energy companies, developers.

Industry/Entity Type

Telecommunications

Contact Information for Business Card

Each card will need the following info:
Persons name:
Title:
E-mail:
Phone number:
Shop Address:
Mailing Address:

Requirements
Must have
• Each card will need the following info:
• Persons name:
• Title:
• E-mail:
• Phone number:
• Shop Address:
• Mailing Address:

```html
<!DOCTYPE html>
<html lang="en">
<head>
<meta charset="utf-8">
<title>Trenchline Civil Inc – Business Card</title>
<link href="https://fonts.googleapis.com/css2?family=Montserrat:wght@500;600;700;800&family=Open+Sans:wght@400;600&display=swap" rel="stylesheet">
<style>
  :root {
    --orange: #e9622a;
    --orange-dark: #c9501e;
    --grey: #6b6d70;
    --grey-dark: #4a4c4f;
    --grey-light: #9a9c9f;
    --text: #6a6a6a;
    --paper: #ffffff;
    --backdrop: #ece9e4;
  }
  * { margin: 0; padding: 0; box-sizing: border-box; }
  html, body {
    width: 1200px; height: 1022px; overflow: hidden;
    background: var(--backdrop);
  }
  .card {
    position: absolute; left: 75px; top: 211px;
    width: 1050px; height: 600px;
    background: var(--paper);
    border-radius: 22px; overflow: hidden;
    box-shadow: 0 10px 30px rgba(0,0,0,.18);
    font-family: "Open Sans", sans-serif;
    color: var(--text);
  }
  .card-bands { position: absolute; inset: 0; }
  .brand {
    position: absolute; left: 70px; top: 90px;
    display: flex; align-items: center; gap: 22px;
  }
  .brand-dot {
    width: 92px; height: 92px; border-radius: 50%;
    background: var(--orange);
  }
  .brand-name {
    font-family: "Montserrat", sans-serif; font-weight: 700;
    font-size: 38px; line-height: 1.05; color: var(--grey);
    letter-spacing: 1px; text-transform: uppercase;
  }
  .divider {
    position: absolute; left: 70px; top: 318px;
    width: 760px; height: 3px; background: var(--orange);
  }
  .person {
    position: absolute; right: 190px; top: 60px;
    text-align: right;
  }
  .person-name {
    font-family: "Montserrat", sans-serif; font-weight: 600;
    font-size: 40px; color: var(--orange); letter-spacing: 1px;
    text-transform: uppercase;
  }
  .person-title { font-size: 22px; margin-top: 4px; }
  .address { font-size: 22px; line-height: 1.35; margin-top: 10px; }
  .address p:nth-child(3), .address p:nth-child(4) { text-transform: uppercase; }
  .contacts {
    position: absolute; left: 70px; top: 345px;
    list-style: none; font-size: 23px; line-height: 1.45;
  }
  .contacts li { display: flex; align-items: center; gap: 16px; }
  .contacts svg { width: 20px; height: 20px; flex: none; }
</style>
</head>
<body>
  <article class="card">
    <svg class="card-bands" viewBox="0 0 1050 600" aria-hidden="true">
      <defs>
        <linearGradient id="band-grey" x1="0" y1="0" x2="1" y2="0">
          <stop offset="0" stop-color="#55575a"/>
          <stop offset=".5" stop-color="#8a8c8f"/>
          <stop offset="1" stop-color="#5a5c5f"/>
        </linearGradient>
        <linearGradient id="band-orange" x1="0" y1="0" x2="0" y2="1">
          <stop offset="0" stop-color="#f0743a"/>
          <stop offset="1" stop-color="#d4561f"/>
        </linearGradient>
      </defs>
      <rect x="930" y="0" width="120" height="48" fill="#4a4c4f"/>
      <path d="M930 64 H1050 V600 H760 L800 530 Q820 500 860 500 H900 Q930 500 930 470 Z" fill="url(#band-grey)"/>
      <rect x="0" y="556" width="790" height="44" fill="url(#band-orange)"/>
    </svg>

    <div class="brand">
      <span class="brand-dot"></span>
      <span class="brand-name">Trenchline<br>Civil Inc</span>
    </div>

    <div class="person">
      <h1 class="person-name">Marcus Hale</h1>
      <p class="person-title">Director</p>
      <div class="address">
        <p>48 Foundry Lane</p>
        <p>Millbrook, NY 12545</p>
        <p>PO Box 3318</p>
        <p>Lakewood, CA 90712</p>
      </div>
    </div>

    <div class="divider"></div>

    <ul class="contacts">
      <li>
        <svg viewBox="0 0 20 20"><rect x="5" y="1.5" width="10" height="17" rx="2" fill="none" stroke="var(--orange)" stroke-width="2"/></svg>
        +330 5182-4406
      </li>
      <li>
        <svg viewBox="0 0 20 20"><path d="M5 2 L8 6 L6 8 Q8 12 12 14 L14 12 L18 15 L16 18 Q8 18 2 5 Z" fill="var(--orange)"/></svg>
        +330 5182-4417
      </li>
      <li>
        <svg viewBox="0 0 20 20"><rect x="1.5" y="4" width="17" height="12" rx="1.5" fill="none" stroke="var(--orange)" stroke-width="2"/><path d="M2 5 L10 11 L18 5" fill="none" stroke="var(--orange)" stroke-width="2"/></svg>
        info@trenchlinecivil.com
      </li>
      <li>
        <svg viewBox="0 0 20 20"><circle cx="10" cy="10" r="8" fill="none" stroke="var(--orange)" stroke-width="2"/><path d="M2 10 H18 M10 2 Q4 10 10 18 M10 2 Q16 10 10 18" fill="none" stroke="var(--orange)" stroke-width="1.5"/></svg>
        www.trenchlinecivil.com
      </li>
    </ul>
  </article>
</body>
</html>
```